Request for Business Card Design

Hi. My name is Marlene, I am looking for a new business card design for my company, Quarrow Signal Instruments, LLC. I really like the design you did for Tarsel Venture and was hoping you could do something similar using our full logo and our mark. I am also open to any raised texture design using our mark. I have attached our full logo, which would need to be somewhere on the card, as well as the mark in both outline and full form, as well as our brand colors / guide. The card does not have to be white, as long as our logo and mark appear. I actually like darker colored business cards more, but am open to all options. If you are interested in working with me, please let me know. We would also take the business card design into letterhead design if you can do that.

```html
<!DOCTYPE html>
<html lang="en">
<head>
<meta charset="utf-8">
<title>Quarrow Signal Instruments – Business Card</title>
<link href="https://fonts.googleapis.com/css2?family=Roboto:wght@400;500;700&display=swap" rel="stylesheet">
<style>
  :root{
    --bg:#2a2a2a;
    --card-dark:#1c1c1d;
    --brand-blue:#1aa3d2;
    --brand-blue-light:#3fc3ec;
    --brand-blue-deep:#0b86b3;
    --ink-white:#ffffff;
    --ink-muted:#d9d9d9;
    --divider:#4a4a4a;
  }
  *{margin:0;padding:0;box-sizing:border-box;}
  html,body{width:1200px;height:689px;overflow:hidden;background:var(--bg);font-family:"Roboto",Arial,sans-serif;}
  .canvas{position:relative;width:1200px;height:689px;}
  .card{position:absolute;top:196px;width:520px;height:297px;border-radius:18px;overflow:hidden;box-shadow:0 18px 40px rgba(0,0,0,.45);}
  .card--front{left:50px;background:linear-gradient(135deg,var(--brand-blue-light),var(--brand-blue) 55%,var(--brand-blue-deep));}
  .card--back{left:630px;background:var(--card-dark);}

  .front-texture{position:absolute;inset:0;background:linear-gradient(160deg,rgba(255,255,255,.12),rgba(0,0,0,.12));}

  .brand{display:flex;align-items:center;color:var(--ink-white);}
  .brand-dot{flex:none;border-radius:50%;}
  .brand-name{font-weight:700;text-transform:uppercase;line-height:1;}
  .brand-name__main{display:block;letter-spacing:3px;}
  .brand-name__sub{display:block;font-weight:500;letter-spacing:1px;margin-top:4px;}

  .front-brand{position:absolute;left:0;right:0;top:114px;justify-content:center;gap:14px;}
  .front-brand .brand-dot{width:44px;height:44px;background:var(--ink-white);}
  .front-brand .brand-name__main{font-size:38px;}
  .front-brand .brand-name__sub{font-size:12px;}

  .back-brand{position:absolute;left:30px;top:126px;gap:10px;}
  .back-brand .brand-dot{width:30px;height:30px;background:var(--brand-blue);}
  .back-brand .brand-name__main{font-size:25px;letter-spacing:2px;}
  .back-brand .brand-name__sub{font-size:8.5px;letter-spacing:.6px;}

  .back-divider{position:absolute;left:262px;top:36px;width:1px;height:180px;background:var(--divider);}
  .contact{position:absolute;left:284px;top:40px;width:216px;color:var(--ink-white);}
  .contact__name{font-size:20px;font-weight:700;color:var(--brand-blue);text-transform:uppercase;letter-spacing:.5px;}
  .contact__title{font-size:13px;margin-bottom:12px;color:var(--ink-muted);}
  .contact__row{display:flex;align-items:center;gap:8px;font-size:12.5px;margin-bottom:5px;white-space:nowrap;}
  .contact__row svg{width:13px;height:13px;flex:none;}
  .contact__address{margin-top:10px;font-size:12.5px;line-height:1.4;padding-left:21px;}
  .back-band{position:absolute;left:0;right:0;bottom:0;width:100%;height:56px;}
</style>
</head>
<body>
<main class="canvas">
  <section class="card card--front" aria-label="Card front">
    <div class="front-texture" role="img" aria-label="Raised pattern of the company mark repeated across the card"></div>
    <div class="brand front-brand">
      <div class="brand-dot"></div>
      <div class="brand-name">
        <span class="brand-name__main">Quarrow</span>
        <span class="brand-name__sub">Signal Instruments</span>
      </div>
    </div>
  </section>

  <section class="card card--back" aria-label="Card back">
    <div class="brand back-brand">
      <div class="brand-dot"></div>
      <div class="brand-name">
        <span class="brand-name__main">Quarrow</span>
        <span class="brand-name__sub">Signal Instruments</span>
      </div>
    </div>
    <div class="back-divider"></div>
    <div class="contact">
      <p class="contact__name">Elias Varno</p>
      <p class="contact__title">Managing Director</p>
      <p class="contact__row">
        <svg viewBox="0 0 24 24"><path fill="#1aa3d2" d="M6.6 10.8a15 15 0 0 0 6.6 6.6l2.2-2.2a1 1 0 0 1 1-.25 11.4 11.4 0 0 0 3.6.57 1 1 0 0 1 1 1V20a1 1 0 0 1-1 1A17 17 0 0 1 3 4a1 1 0 0 1 1-1h3.5a1 1 0 0 1 1 1c0 1.25.2 2.450.57 3.57a1 1 0 0 1-.25 1z"/></svg>
        044-555 010 246
      </p>
      <p class="contact__row">
        <svg viewBox="0 0 24 24"><rect x="2" y="5" width="20" height="14" rx="1.5" fill="#1aa3d2"/><path d="M3 6l9 7 9-7" stroke="#1c1c1d" stroke-width="1.8" fill="none"/></svg>
        info@quarrowsignal.com
      </p>
      <p class="contact__row">
        <svg viewBox="0 0 24 24" fill="none" stroke="#1aa3d2" stroke-width="2"><circle cx="12" cy="12" r="9"/><path d="M3 12h18M12 3c3 3 3 15 0 18M12 3c-3 3-3 15 0 18"/></svg>
        www.quarrowsignal.com
      </p>
      <p class="contact__address">78, Fenwick Lane, Suite 4<br>30418, Northvale</p>
    </div>
    <svg class="back-band" viewBox="0 0 520 56" preserveAspectRatio="none" aria-hidden="true">
      <rect x="0" y="14" width="520" height="3" fill="#1aa3d2"/>
      <rect x="0" y="24" width="520" height="32" fill="#1aa3d2"/>
    </svg>
  </section>
</main>
</body>
</html>
```